wardrobe/costume stylist needs good business card for own business

Hi:)

I'm wanting a business card for my company. I am a freelance stylist.

I do wardrobe/costume stylist to TV commercials; Films; Fashion and Lifestyle shoots.

I'd like a design based around my name Rosalind Parfrey written nicely, maybe a colour? Up to you?!

I've attached a couple of images of business cards I like
.... be creative and have fun!

Thank you :)

Reason: I was trying to get my new business card ready for before I headed overseas Friday morning but I don't think that was realistic so I'd like to extend the deadline to give time to the project. Thank you

Hi designers:) Thank you for all your designs, I've extended the deadline until Sunday, so there's a bit more time. I've attached 3 pictures of business cards which I quite like, please take a look to see if it can be of help in your process. I like the pale plain or patterned background with dark font and the dark plain or patterned background with the pale font the motifs the feminine fonts the plain fonts I like the idea of playing with a circle or some shape on one side of the card with my name or initials as in the picture I have on my post could you play around with this idea a bit please? Thank you all for the work you've done :) Rosa

Hi I am working overseas til Saturday night sorry for no feedback until I teturn Thanks :) Rosa

Hi designers, Thank you all so much for submitting your designs, I really appreciate your input into my project :) I'm sorry I didn't get to respond to some comments, and give feedback. I didn't back from being away until later than I expected, and the deadline had passed then, so apologies. Thanks to you all again for all your really good designs :) Rosa

Target Market(s)

I am a freelance stylist my target audience is producers, production companies, photographers, directors...

Industry/Entity Type

Business

Requirements
Must have
• Rosalind Parfrey
Stylist or Wardrobe Stylist

email rosaparfrey@mailbox-example.co.nz
Mobile 0218467193

(Don't have to use the words 'email' and 'mobile')
Nice to have
• Would like it to be double sided
Like B & W
Like pale colour background with dark font or white font
Like dark colour background with pale font
Should not have
• I would prefer it not to incorporate pictures

```html
<!DOCTYPE html>
<html lang="en">
<head>
<meta charset="utf-8">
<title>Rosalind Parfrey – Wardrobe Stylist Business Cards</title>
<link rel="stylesheet" href="https://fonts.googleapis.com/css2?family=Grand+Hotel&family=Josefin+Sans:wght@300;400;700&display=swap">
<style>
  :root {
    --teal: #17a79e;
    --teal-deep: #0f8f88;
    --teal-soft: #8fd6d1;
    --paper: #f4f4f2;
    --white: #ffffff;
    --backdrop: #dcdcda;
    --script: "Grand Hotel", cursive;
    --sans: "Josefin Sans", sans-serif;
  }
  * { box-sizing: border-box; margin: 0; padding: 0; }
  html, body {
    width: 1200px;
    height: 900px;
    overflow: hidden;
    background: var(--backdrop);
  }
  .canvas {
    width: 1200px;
    height: 900px;
    display: flex;
    align-items: center;
    justify-content: center;
    gap: 40px;
  }
  .card {
    position: relative;
    width: 540px;
    height: 310px;
    border-radius: 4px;
    overflow: hidden;
    box-shadow: 0 10px 30px rgba(0,0,0,0.18);
  }

  /* Back: contact side */
  .card--contact {
    background: linear-gradient(160deg, var(--teal) 0%, var(--teal-deep) 100%);
    color: var(--white);
  }
  .card--contact .ornament {
    background: radial-gradient(ellipse at 20% 45%, rgba(255,255,255,0.55) 0%, rgba(255,255,255,0.2) 45%, rgba(255,255,255,0) 75%);
  }
  .contact-block {
    position: absolute;
    left: 230px;
    top: 70px;
  }
  .contact-name {
    font-family: var(--script);
    font-size: 34px;
    line-height: 1;
  }
  .contact-role {
    font-family: var(--sans);
    font-weight: 300;
    font-size: 11px;
    letter-spacing: 1.5px;
    text-transform: uppercase;
    margin: 6px 0 18px 4px;
  }
  .contact-row {
    display: flex;
    align-items: baseline;
    font-family: var(--sans);
    font-weight: 300;
    font-size: 17px;
    margin-bottom: 12px;
  }
  .contact-label {
    width: 34px;
    font-weight: 700;
    font-size: 18px;
  }

  /* Front: name side */
  .card--name {
    background: var(--paper);
    color: var(--teal);
  }
  .card--name .ornament {
    background: radial-gradient(ellipse at 20% 45%, rgba(23,167,158,0.55) 0%, rgba(23,167,158,0.2) 45%, rgba(23,167,158,0) 75%);
  }
  .name-block {
    position: absolute;
    left: 220px;
    top: 105px;
    text-align: center;
  }
  .name-title {
    font-family: var(--script);
    font-size: 50px;
    line-height: 1;
  }
  .name-role {
    font-family: var(--sans);
    font-weight: 300;
    font-size: 14px;
    letter-spacing: 5px;
    text-transform: uppercase;
    margin-top: 8px;
    padding-top: 8px;
    border-top: 1px solid var(--teal);
  }

  .ornament {
    position: absolute;
    left: 0;
    top: 0;
    width: 210px;
    height: 100%;
  }
</style>
</head>
<body>
  <main class="canvas">
    <section class="card card--contact">
      <div class="ornament" role="img" aria-label="Flowing white swirl ornament with curling tendrils and droplets along the left edge"></div>
      <div class="contact-block">
        <p class="contact-name">Rosalind Parfrey</p>
        <p class="contact-role">Wardrobe Stylist</p>
        <p class="contact-row"><span class="contact-label">M</span><span>0218467193</span></p>
        <p class="contact-row"><span class="contact-label">E</span><span>rosaparfrey@mailbox-example.co.nz</span></p>
      </div>
    </section>

    <section class="card card--name">
      <div class="ornament" role="img" aria-label="Flowing teal swirl ornament with curling tendrils and droplets along the left edge"></div>
      <div class="name-block">
        <h1 class="name-title">Rosalind Parfrey</h1>
        <p class="name-role">Wardrobe Stylist</p>
      </div>
    </section>
  </main>
</body>
</html>
```